Design my business card

I require a business card design ready to send to a professional printers.

here are the requirements:
- please use the below link as a rough guide
- dimensions are 85mm x 55mm, with safety space around it
- please use any sample value for the name/email/etc. I'll pass the real details on to the winner.
- I need two versions, with blue and orange, per the attached images

In order to be accepted for this context, please quote X974 in your response. Entry costs accepted are below 40 euro only. Anything above 40 euro or not quoting the text are rejected sorry!

I can attach adobe illustrator version of the logo if its needed

```html
<!DOCTYPE html>
<html lang="en">
<head>
<meta charset="utf-8">
<title>Quantivo Business Cards</title>
<link rel="stylesheet" href="https://fonts.googleapis.com/css2?family=Open+Sans:wght@300;400&display=swap">
<style>
  :root {
    --backdrop: #5b5d61;
    --card-blue: #3b5bae;
    --card-orange: #ee9427;
    --ink: #1b1d2b;
    --accent: #2c7cc2;
  }
  * { margin: 0; padding: 0; box-sizing: border-box; }
  html, body { width: 1200px; height: 900px; overflow: hidden; }
  body {
    background: var(--backdrop);
    font-family: "Open Sans", Arial, sans-serif;
    color: var(--ink);
    position: relative;
  }
  .card {
    position: absolute;
    width: 620px;
    height: 401px;
    box-shadow: 0 10px 24px rgba(0,0,0,0.35);
  }
  .card--back { left: 150px; top: 40px; background: var(--card-blue); }
  .card--front { left: 430px; top: 465px; background: var(--card-orange); }

  .wordmark {
    position: absolute;
    font-weight: 300;
    letter-spacing: 1px;
    line-height: 1;
    color: var(--ink);
    white-space: nowrap;
  }
  .card--back .wordmark { left: 50%; top: 120px; transform: translateX(-50%); font-size: 104px; }
  .card--front .wordmark { left: 60px; top: 70px; font-size: 96px; }

  .web-line {
    position: absolute;
    left: 50%;
    top: 300px;
    transform: translateX(-50%);
    display: flex;
    align-items: center;
    gap: 12px;
    font-size: 17px;
    white-space: nowrap;
  }
  .icon { width: 18px; height: 18px; flex: none; }

  .person { position: absolute; left: 60px; top: 268px; text-align: right; }
  .person__name { font-size: 30px; font-weight: 400; line-height: 1.1; }
  .person__role { font-size: 14px; font-weight: 400; }

  .divider {
    position: absolute;
    left: 316px; top: 200px;
    width: 2px; height: 150px;
    background: var(--accent);
  }

  .contact-list {
    position: absolute;
    left: 336px; top: 196px;
    list-style: none;
  }
  .contact-list li {
    display: flex;
    align-items: center;
    gap: 14px;
    font-size: 17px;
    height: 38px;
    white-space: nowrap;
  }
</style>
</head>
<body>

  <section class="card card--back" aria-label="Card back">
    <div class="wordmark">quantivo</div>
    <div class="web-line">
      <svg class="icon" viewBox="0 0 20 20" aria-hidden="true">
        <circle cx="10" cy="10" r="8" fill="none" stroke="#1b1d2b" stroke-width="1.6"/>
        <ellipse cx="10" cy="10" rx="3.5" ry="8" fill="none" stroke="#1b1d2b" stroke-width="1.4"/>
        <line x1="2" y1="10" x2="18" y2="10" stroke="#1b1d2b" stroke-width="1.4"/>
      </svg>
      <span>www.westfieldtrading.com</span>
    </div>
  </section>

  <section class="card card--front" aria-label="Card front">
    <div class="wordmark">quantivo</div>

    <div class="person">
      <p class="person__name">Lars Hemming</p>
      <p class="person__role">CEO</p>
    </div>

    <div class="divider"></div>

    <ul class="contact-list">
      <li>
        <svg class="icon" viewBox="0 0 20 20" aria-hidden="true">
          <path d="M5 2 L8 6 L6.5 8 Q8 11.5 12 13.5 L14 12 L18 15 L16 18 Q9 18 2 9 Q2 4 5 2 Z" fill="none" stroke="#1b1d2b" stroke-width="1.5" stroke-linejoin="round"/>
        </svg>
        <span>613 528 904</span>
      </li>
      <li>
        <svg class="icon" viewBox="0 0 20 20" aria-hidden="true">
          <rect x="5" y="2" width="10" height="5" fill="#1b1d2b"/>
          <rect x="2" y="7" width="16" height="7" rx="1" fill="#1b1d2b"/>
          <rect x="5" y="12" width="10" height="6" fill="#ffffff" stroke="#1b1d2b" stroke-width="1.4"/>
        </svg>
        <span>613 207 3385</span>
      </li>
      <li>
        <svg class="icon" viewBox="0 0 20 20" aria-hidden="true">
          <circle cx="10" cy="10" r="8" fill="#1b1d2b"/>
          <ellipse cx="10" cy="10" rx="3.5" ry="8" fill="none" stroke="#ee9427" stroke-width="1.2"/>
          <line x1="2" y1="10" x2="18" y2="10" stroke="#ee9427" stroke-width="1.2"/>
        </svg>
        <span>westfieldtrading.com</span>
      </li>
      <li>
        <svg class="icon" viewBox="0 0 20 20" aria-hidden="true">
          <rect x="2" y="4" width="16" height="12" fill="#1b1d2b"/>
          <path d="M2 4 L10 11 L18 4" fill="none" stroke="#ffffff" stroke-width="1.4"/>
        </svg>
        <span>lars@westfieldtrading</span>
      </li>
    </ul>
  </section>

</body>
</html>
```